Animal Eye Clinic needs a Business card

We are a new veterinary ophthalmology practice (Ridgeline Pet Vision Care) and we need a business card designed. We only see animal eyes - we are not a regular veterinary clinic. We already have a logo. We are looking for a professional, good looking business card to hand out to our clients. We are looking for something simple but professional and contemporary. Our logo is likely the only picture/graphic that needs to be on the card.
Updates

Contact Information for Business Card

Delia Vossman, BSc, DVM, MSc, DipACVO
Veterinary Ophthalmologist

Phone: 250.418.3927
Email: ridgelinepetvisioncare@mailbox-example.net
Website: ridgelinepetvisioncare-example.net
Address: 1874 Thornbury Rd
Kelowna, BC, V1X 4M9

Colors

Designer to choose colors to be used in the design.

Requirements
Must have
• Our logo (attached)

```html
<!DOCTYPE html>
<html lang="en">
<head>
<meta charset="utf-8">
<title>Ridgeline Pet Vision Care – Business Card</title>
<link rel="stylesheet" href="https://fonts.googleapis.com/css2?family=Roboto:wght@400;500&display=swap">
<style>
  :root {
    --backdrop: #2e2926;
    --card: #6b6b6d;
    --card-shade: #5e5e60;
    --teal: #1a9aa8;
    --white: #f4f4f4;
    --emboss-light: #77777a;
    --emboss-dark: #4f4f52;
  }
  * { margin: 0; padding: 0; box-sizing: border-box; }
  html, body { width: 1200px; height: 847px; overflow: hidden; }
  body {
    background: var(--backdrop);
    font-family: "Roboto", Arial, sans-serif;
    position: relative;
  }
  .card {
    position: absolute;
    top: 260px;
    width: 520px;
    height: 297px;
    background: var(--card);
    border-bottom: 5px solid var(--teal);
    box-shadow: 0 10px 24px rgba(0,0,0,.45);
    overflow: hidden;
  }
  .card--front { left: 50px; }
  .card--back { left: 630px; }

  .brand { display: flex; align-items: center; color: var(--teal); font-weight: 500; }
  .brand__dot { border-radius: 50%; background: var(--teal); flex: none; }

  .card--front .brand {
    position: absolute; left: 0; right: 0; top: 0; bottom: 0;
    justify-content: center; gap: 14px; font-size: 24px;
  }
  .card--front .brand__dot { width: 34px; height: 34px; }

  .card--back .brand { position: absolute; left: 26px; top: 24px; gap: 9px; font-size: 15px; }
  .card--back .brand__dot { width: 20px; height: 20px; }

  .contact { position: absolute; left: 26px; top: 74px; color: var(--white); font-size: 12px; line-height: 1.45; }
  .contact__name { color: var(--teal); font-size: 17px; font-weight: 500; text-transform: uppercase; letter-spacing: .5px; }
  .contact__creds { color: var(--teal); font-size: 11px; }
  .contact__title { margin-bottom: 12px; }
  .contact__address { margin-bottom: 10px; }
  .contact__row { display: flex; align-items: center; gap: 6px; font-size: 11.5px; }
  .contact__row svg { width: 10px; height: 10px; flex: none; fill: var(--teal); }

  .illustration {
    position: absolute; right: 0; top: 80px; width: 210px; height: 212px;
    background: radial-gradient(ellipse at 60% 40%, var(--emboss-light), var(--card-shade) 60%, var(--emboss-dark));
    border-top-left-radius: 60% 50%;
    opacity: .85;
  }
</style>
</head>
<body>
  <section class="card card--front" aria-label="Card front">
    <div class="brand">
      <span class="brand__dot"></span>
      <span class="brand__name">Ridgeline Pet Vision Care</span>
    </div>
  </section>

  <section class="card card--back" aria-label="Card back">
    <div class="brand">
      <span class="brand__dot"></span>
      <span class="brand__name">Ridgeline Pet Vision Care</span>
    </div>

    <div class="contact">
      <p class="contact__name">Delia Vossman</p>
      <p class="contact__creds">BSc, DVM, MSc, DipACVO</p>
      <p class="contact__title">Veterinary Ophthalmologist</p>
      <p class="contact__address">1874 Thornbury Rd<br>Kelowna, BC, V1X 4M9</p>
      <p class="contact__row">
        <svg viewBox="0 0 10 10" aria-hidden="true"><path d="M2 0.5 L3.6 0.5 L4.2 3 L3 3.8 Q4 6 6.2 7 L7 5.8 L9.5 6.4 L9.5 8 Q9.5 9.5 8 9.5 Q0.5 9 0.5 2 Q0.5 0.5 2 0.5Z"/></svg>
        250.418.3927
      </p>
      <p class="contact__row">
        <svg viewBox="0 0 10 10" aria-hidden="true"><path d="M0.5 2 H9.5 V8 H0.5Z M0.5 2 L5 5.5 L9.5 2" /></svg>
        ridgelinepetvisioncare@mailbox-example.net
      </p>
      <p class="contact__row">
        <svg viewBox="0 0 10 10" aria-hidden="true"><circle cx="5" cy="5" r="4.5"/></svg>
        ridgelinepetvisioncare-example.net
      </p>
    </div>

    <div class="illustration" role="img" aria-label="Blind-embossed silhouettes of a horse, cat and dog"></div>
  </section>
</body>
</html>
```